Create a premium soap bar box bar design for an all-natural, men's skincare brand.

We are launching a men’s premium, natural soap bar and skincare business. To start, we will be launching cold-press, all-natural soap bars with a few additional products such as lotions. We plan to expand our line into additional skincare products such as face exfoliants, moisturizers and cleansers that target basic needs such as anti-aging, clarifying and hydrating.

Our target audience is men ages 25-50, with a secondary audience of male teens. Our target audience are mid to high income, professionals that live in more urban areas, but enjoy being active outdoors after work and on the weekends. Our target audience are hard workers, humble and want to enjoy all that life has to offer – whether that’s on top of a mountain or an ocean wave. They hike, bike, skateboard, surf or any other sport that gets them outside. They are husbands, brothers and fathers – there for their family and friends.

Our brand is sophisticated, adventurous and has a sense of humor. Many of our competitors either focus on the rugged outdoors or are more pretentious. We are in-between. We are free spirited and love the fresh air. Our products are trustworthy with no toxic chemicals or harsh ingredients. We are all-natural and provide high-quality, premium products that our audience expects and deserves.

Target Market(s)

Men, ages 25-54 who are high-earning professionals, yet enjoy getting outdoors and being active on the weekends - hiking, biking, surfing, skateboarding and more.

Industry/Entity Type

Men's skincare

Font styles to use
Sans Serif

Requirements
Must have
• See attachments
Nice to have
• We would prefer to a have a premium, slightly more modern looking design that will appeal to our target audience and slightly higher price point.
Should not have
• Please do not include an icon for the fragrance, i.e. cinnamon sticks. However, we do need some differentiation for the fragrance, i.e. color, etc. as it will be on the shelf with other fragrances.

```html
<!DOCTYPE html>
<html lang="en">
<head>
<meta charset="utf-8">
<title>Hal Rowan Soap Labels</title>
<link rel="stylesheet" href="https://fonts.googleapis.com/css2?family=Alfa+Slab+One&family=Oswald:wght@300;400&family=Montserrat:wght@400;500&display=swap">
<style>
  :root {
    --backdrop: #e9e5e4;
    --navy: #0e2a46;
    --kraft: #c8a67b;
    --white: #ffffff;
    --green: #0b7a12;
    --orange: #d4640a;
    --maroon: #780606;
    --slab: "Alfa Slab One", Georgia, serif;
    --condensed: "Oswald", "Arial Narrow", sans-serif;
    --sans: "Montserrat", Arial, sans-serif;
  }
  * { margin: 0; padding: 0; box-sizing: border-box; }
  html, body { width: 1200px; height: 864px; overflow: hidden; background: var(--backdrop); }
  .canvas { position: relative; width: 1200px; height: 864px; }

  .label { position: absolute; top: 170px; width: 341px; height: 541px; overflow: hidden; color: var(--navy); }
  .label--citrus { left: 57px; --accent: var(--green); }
  .label--cinnamon { left: 430px; --accent: var(--orange); }
  .label--bourbon { left: 803px; --accent: var(--maroon); }

  .label__shapes { position: absolute; inset: 0; }
  .shape--kraft { fill: var(--kraft); }
  .shape--navy { fill: var(--navy); }
  .shape--accent { fill: var(--accent); }

  .label > div, .label > p, .label > h2, .label > h3 { position: absolute; }

  .side-title { left: 14px; top: 16px; font-family: var(--slab); font-size: 14px; line-height: 14px; color: var(--white); letter-spacing: 0.5px; }
  .info { left: 14px; top: 67px; width: 136px; color: var(--white); }
  .info h4 { font-family: var(--slab); font-weight: 400; font-size: 9.5px; letter-spacing: 1px; line-height: 12px; }
  .info p { font-family: var(--condensed); font-weight: 300; font-size: 9.6px; line-height: 12.3px; }
  .info .directions { margin-top: 8px; }

  .pitch { left: 130px; top: 13px; width: 200px; text-align: center; }
  .pitch h3 { font-family: var(--slab); font-weight: 400; font-size: 12px; line-height: 13px; letter-spacing: 1.6px; }
  .pitch p { margin: 7px 0 0 22px; width: 170px; font-family: var(--condensed); font-weight: 300; font-size: 9.2px; line-height: 12.3px; }

  .brand-small { left: 214px; top: 190px; display: flex; align-items: center; gap: 4px; font-family: var(--sans); font-weight: 500; font-size: 10px; letter-spacing: 0.8px; color: var(--navy); }
  .brand-small .dot { width: 13px; height: 13px; border-radius: 50%; background: #d8433c; }
  .origin-badge { left: 299px; top: 179px; width: 34px; height: 34px; background: var(--white); }

  .perks { left: 14px; top: 228px; font-family: var(--condensed); font-weight: 300; font-size: 10.5px; line-height: 16px; color: var(--white); }
  .perks span { margin-right: 10px; }
  .shop { left: 217px; top: 229px; font-family: var(--condensed); font-weight: 300; font-size: 10px; line-height: 13px; color: var(--white); }
  .shop strong { display: block; font-family: var(--slab); font-weight: 400; font-size: 9.6px; letter-spacing: 1px; }

  .brand-main { left: 10px; top: 318px; width: 120px; text-align: center; color: var(--white); }
  .brand-main .ring { display: block; width: 38px; height: 38px; margin: 0 auto 8px; border-radius: 50%; border: 2.5px solid var(--white); }
  .brand-main .name { font-family: var(--sans); font-weight: 500; font-size: 15px; letter-spacing: 1.2px; line-height: 16px; }
  .brand-main .tag { font-family: var(--sans); font-size: 4.6px; letter-spacing: 2.6px; margin-top: 3px; }

  .scent { left: 0; top: 301px; width: 341px; font-family: var(--slab); font-weight: 400; font-size: 32px; line-height: 28px; color: var(--accent); }
  .scent span { display: block; white-space: nowrap; }
  .notes { left: 159px; top: 397px; }
  .notes h3 { font-family: var(--sans); font-weight: 400; font-size: 12px; letter-spacing: 1.2px; line-height: 15px; }
  .notes p { font-family: var(--sans); font-size: 9px; letter-spacing: 0.3px; }
  .grit { left: 266px; top: 419px; width: 60px; height: 60px; border: 2px dashed var(--navy); border-radius: 50%; display: flex; align-items: center; justify-content: center; transform: rotate(12deg); }
  .grit span { font-family: var(--condensed); font-weight: 400; font-size: 9px; letter-spacing: 0.4px; color: var(--accent); white-space: nowrap; }
  .weight { left: 126px; top: 468px; font-family: var(--sans); font-size: 8.8px; }

  .distributor { left: 141px; top: 507px; font-family: var(--condensed); font-weight: 300; font-size: 9.6px; line-height: 12.5px; color: var(--white); }
</style>
</head>
<body>
<main class="canvas">

  <!-- Citrus and Cedar -->
  <article class="label label--citrus">
    <svg class="label__shapes" viewBox="0 0 341 541" aria-hidden="true">
      <rect class="shape--kraft" width="341" height="541"/>
      <polygon class="shape--navy" points="0,0 116,0 203,220 0,220"/>
      <polygon class="shape--accent" points="116,0 123,0 210,220 203,220"/>
      <polygon class="shape--navy" points="0,220 203,220 186,270 0,270"/>
      <polygon class="shape--accent" points="203,220 341,220 341,270 186,270"/>
      <polygon class="shape--navy" points="0,270 186,270 96,490 0,490"/>
      <polygon class="shape--accent" points="186,270 193,270 103,490 96,490"/>
      <rect class="shape--accent" y="490" width="341" height="51"/>
    </svg>
    <h2 class="side-title">CITRUS<br>AND<br>CEDAR</h2>
    <div class="info">
      <h4>INGREDIENTS:</h4>
      <p>Vegetable Oil Blend (Olive Oil, Organic Sustainable Palm Oil, Coconut Oil, Shea Butter, Sunflower Oil), Water, Sodium Hydroxide, Beeswax, Cinnamon Essential Oil, Honey, Ground Cinnamon.</p>
      <h4 class="directions">DIRECTIONS:</h4>
      <p>Lather, rinse and repeat.</p>
    </div>
    <div class="pitch">
      <h3>REAL INGREDIENTS<br>FOR REAL GUYS.</h3>
      <p>Bring the outdoors in using real, natural ingredients on your skin. Traditional bar soap contains harsh chemical ingredients that can be harmful to you and the environment. Lather up with Hal Rowan's handcrafted, all-natural soap and feel the difference.</p>
    </div>
    <div class="brand-small"><span class="dot"></span>HAL ROWAN</div>
    <div class="origin-badge"></div>
    <div class="perks"><span>✓Handcrafted</span><span>✓No harsh chemicals</span><br><span>✓Sustainably sourced</span></div>
    <div class="shop">Check out all our products at<strong>HALROWAN.COM</strong></div>
    <div class="brand-main"><span class="ring"></span><div class="name">HAL ROWAN</div><div class="tag">REAL SKINCARE</div></div>
    <h2 class="scent"><span style="margin-left:178px">CITRUS</span><span style="margin-left:190px">AND</span><span style="margin-left:160px">CEDAR</span></h2>
    <div class="notes"><h3>SWEET &amp; SPICY</h3><p>Men's Natural Soap</p></div>
    <div class="grit"><span>MEDIUM GRIT</span></div>
    <p class="weight">5 Oz. Bar</p>
    <p class="distributor">Distributed by:<br>K&amp;M Goods Duluth, MN 55802</p>
  </article>

  <!-- Cinnamon Bark -->
  <article class="label label--cinnamon">
    <svg class="label__shapes" viewBox="0 0 341 541" aria-hidden="true">
      <rect class="shape--kraft" width="341" height="541"/>
      <polygon class="shape--navy" points="0,0 116,0 203,220 0,220"/>
      <polygon class="shape--accent" points="116,0 123,0 210,220 203,220"/>
      <polygon class="shape--navy" points="0,220 203,220 186,270 0,270"/>
      <polygon class="shape--accent" points="203,220 341,220 341,270 186,270"/>
      <polygon class="shape--navy" points="0,270 186,270 96,490 0,490"/>
      <polygon class="shape--accent" points="186,270 193,270 103,490 96,490"/>
      <rect class="shape--accent" y="490" width="341" height="51"/>
    </svg>
    <h2 class="side-title">CINNA<br>MON<br>BARK</h2>
    <div class="info">
      <h4>INGREDIENTS:</h4>
      <p>Vegetable Oil Blend (Olive Oil, Organic Sustainable Palm Oil, Coconut Oil, Shea Butter, Sunflower Oil), Water, Sodium Hydroxide, Beeswax, Cinnamon Essential Oil, Honey, Ground Cinnamon.</p>
      <h4 class="directions">DIRECTIONS:</h4>
      <p>Lather, rinse and repeat.</p>
    </div>
    <div class="pitch">
      <h3>REAL INGREDIENTS<br>FOR REAL GUYS.</h3>
      <p>Bring the outdoors in using real, natural ingredients on your skin. Traditional bar soap contains harsh chemical ingredients that can be harmful to you and the environment. Lather up with Hal Rowan's handcrafted, all-natural soap and feel the difference.</p>
    </div>
    <div class="brand-small"><span class="dot"></span>HAL ROWAN</div>
    <div class="origin-badge"></div>
    <div class="perks"><span>✓Handcrafted</span><span>✓No harsh chemicals</span><br><span>✓Sustainably sourced</span></div>
    <div class="shop">Check out all our products at<strong>HALROWAN.COM</strong></div>
    <div class="brand-main"><span class="ring"></span><div class="name">HAL ROWAN</div><div class="tag">REAL SKINCARE</div></div>
    <h2 class="scent"><span style="margin-left:185px">CINNA</span><span style="margin-left:226px">MON</span><span style="margin-left:160px">BARK</span></h2>
    <div class="notes"><h3>SWEET &amp; SPICY</h3><p>Men's Natural Soap</p></div>
    <div class="grit"><span>MEDIUM GRIT</span></div>
    <p class="weight">5 Oz. Bar</p>
    <p class="distributor">Distributed by:<br>K&amp;M Goods Duluth, MN 55802</p>
  </article>

  <!-- Bourbon Vanilla -->
  <article class="label label--bourbon">
    <svg class="label__shapes" viewBox="0 0 341 541" aria-hidden="true">
      <rect class="shape--kraft" width="341" height="541"/>
      <polygon class="shape--navy" points="0,0 116,0 203,220 0,220"/>
      <polygon class="shape--accent" points="116,0 123,0 210,220 203,220"/>
      <polygon class="shape--navy" points="0,220 203,220 186,270 0,270"/>
      <polygon class="shape--accent" points="203,220 341,220 341,270 186,270"/>
      <polygon class="shape--navy" points="0,270 186,270 96,490 0,490"/>
      <polygon class="shape--accent" points="186,270 193,270 103,490 96,490"/>
      <rect class="shape--accent" y="490" width="341" height="51"/>
    </svg>
    <h2 class="side-title">BOUR<br>BON<br>VANILLA</h2>
    <div class="info">
      <h4>INGREDIENTS:</h4>
      <p>Vegetable Oil Blend (Olive Oil, Organic Sustainable Palm Oil, Coconut Oil, Shea Butter, Sunflower Oil), Water, Sodium Hydroxide, Beeswax, Cinnamon Essential Oil, Honey, Ground Cinnamon.</p>
      <h4 class="directions">DIRECTIONS:</h4>
      <p>Lather, rinse and repeat.</p>
    </div>
    <div class="pitch">
      <h3>REAL INGREDIENTS<br>FOR REAL GUYS.</h3>
      <p>Bring the outdoors in using real, natural ingredients on your skin. Traditional bar soap contains harsh chemical ingredients that can be harmful to you and the environment. Lather up with Hal Rowan's handcrafted, all-natural soap and feel the difference.</p>
    </div>
    <div class="brand-small"><span class="dot"></span>HAL ROWAN</div>
    <div class="origin-badge"></div>
    <div class="perks"><span>✓Handcrafted</span><span>✓No harsh chemicals</span><br><span>✓Sustainably sourced</span></div>
    <div class="shop">Check out all our products at<strong>HALROWAN.COM</strong></div>
    <div class="brand-main"><span class="ring"></span><div class="name">HAL ROWAN</div><div class="tag">REAL SKINCARE</div></div>
    <h2 class="scent"><span style="margin-left:185px">BOUR</span><span style="margin-left:206px">BON</span><span style="margin-left:153px">VANILLA</span></h2>
    <div class="notes"><h3>SWEET &amp; SPICY</h3><p>Men's Natural Soap</p></div>
    <div class="grit"><span>MEDIUM GRIT</span></div>
    <p class="weight">5 Oz. Bar</p>
    <p class="distributor">Distributed by:<br>K&amp;M Goods Duluth, MN 55802</p>
  </article>

</main>
</body>
</html>
```